Stylish business cards for KV7

To create an appealing and professional business card design for a WOMEN Owned Construction Supply Company.
2 sided card. Incorporate brand elements, curvy, colorful, sleek and bright. No solid white background. attached samples of styles added shapes/ribbons. Want something with that WOW that looks awesome, factor. It is a new logo, so feel free to mess with logo colors in the blue and teal factors that can look good with both dark and light background. If you want to try a watermark with just the KV7, without the "Supply" that might look cool to.

Industry/Entity Type

Women owned construction supply company

Contact Information for Business Card

Name, Title, and phone number and email, web page. maybe spot for qr code.

Font styles to use
Sans Serif

Requirements
Nice to have
• would love to see colors, maybe stylish ribbon dividers or some sort of 2 or 3 tone color card that compliments logo.
Should not have
• Please do not have all white background. Do not include Home/reale state/ or building images.

```html
<!DOCTYPE html>
<html lang="en">
<head>
<meta charset="utf-8">
<title>KV7 Supply – Business Cards</title>
<link rel="stylesheet" href="https://fonts.googleapis.com/css2?family=Montserrat:wght@400;500;700&display=swap">
<style>
  :root {
    --backdrop: #1b1b1c;
    --card-navy: #1c3a5b;
    --teal: #2a9dc4;
    --white: #ffffff;
    --text-light: #f2f5f8;
  }
  * { margin: 0; padding: 0; box-sizing: border-box; }
  html, body {
    width: 1200px; height: 1059px; overflow: hidden;
    background: var(--backdrop);
    font-family: "Montserrat", sans-serif;
  }
  .canvas { position: relative; width: 1200px; height: 1059px; }
  .card {
    position: absolute; left: 255px; width: 690px; height: 392px;
    background: var(--card-navy); border-radius: 22px; overflow: hidden;
  }
  .card--front { top: 89px; }
  .card--back { top: 546px; }

  .brand-mark {
    position: absolute; left: 32px; top: 56px;
    font-size: 30px; font-weight: 700; color: var(--white);
    letter-spacing: 0.5px;
  }
  .accent-bar {
    position: absolute; left: 0; top: 191px; width: 17px; height: 35px;
    background: var(--teal);
  }
  .contact { position: absolute; left: 32px; top: 188px; color: var(--text-light); }
  .contact__name { font-size: 22px; font-weight: 700; color: var(--teal); line-height: 1.1; }
  .contact__title { font-size: 15px; font-weight: 400; margin-top: 3px; }
  .contact__address { font-size: 15px; line-height: 20px; margin-top: 14px; }
  .contact__list { list-style: none; margin-top: 12px; }
  .contact__item {
    display: flex; align-items: center; gap: 7px;
    font-size: 15px; height: 25px;
  }
  .contact__item svg { width: 12px; height: 12px; flex: none; }

  .watermark {
    position: absolute; right: 20px; bottom: 40px;
    font-size: 190px; font-weight: 700; color: var(--white);
    line-height: 1; letter-spacing: -4px;
  }

  .back-brand {
    position: absolute; left: 0; right: 0; top: 50%;
    transform: translateY(-50%);
    text-align: center; font-size: 66px; font-weight: 700;
    color: var(--white); letter-spacing: 1px;
  }
</style>
</head>
<body>
<main class="canvas">
  <section class="card card--front" aria-label="Business card front">
    <div class="brand-mark">KV7 Supply</div>
    <div class="accent-bar"></div>
    <div class="contact">
      <h1 class="contact__name">DANA WHITFIELD</h1>
      <p class="contact__title">CEO/Founder</p>
      <p class="contact__address">P.O Box 4127 Harbour Road<br>Brookvale NS 20100</p>
      <ul class="contact__list">
        <li class="contact__item">
          <svg viewBox="0 0 24 24" aria-hidden="true"><path fill="#2a9dc4" d="M6.6 10.8a15.1 15.1 0 0 0 6.6 6.6l2.2-2.2a1 1 0 0 1 1-.25 11.4 11.4 0 0 0 3.6.57 1 1 0 0 1 1 1V20a1 1 0 0 1-1 1A17 17 0 0 1 3 4a1 1 0 0 1 1-1h3.5a1 1 0 0 1 1 1c0 1.25.2 2.46.57 3.6a1 1 0 0 1-.25 1z"/></svg>
          402.318.7754
        </li>
        <li class="contact__item">
          <svg viewBox="0 0 24 24" aria-hidden="true"><rect x="2" y="5" width="20" height="14" fill="none" stroke="#2a9dc4" stroke-width="2"/><path d="M2 5l10 8 10-8" fill="none" stroke="#2a9dc4" stroke-width="2"/></svg>
          info@kv7supply.com.au
        </li>
        <li class="contact__item">
          <svg viewBox="0 0 24 24" aria-hidden="true"><g fill="none" stroke="#2a9dc4" stroke-width="2"><circle cx="12" cy="12" r="10"/><ellipse cx="12" cy="12" rx="4" ry="10"/><path d="M2 12h20M4 7h16M4 17h16"/></g></svg>
          www.kv7supply.com.au
        </li>
      </ul>
    </div>
    <div class="watermark" aria-hidden="true">KV7</div>
  </section>

  <section class="card card--back" aria-label="Business card back">
    <div class="back-brand">KV7 Supply</div>
  </section>
</main>
</body>
</html>
```